Brivelo - a brand new platform for targetted offers

Hello there, art hive!
As a new business we want to build a mobile web site (that later will be converted to mobile app) that will allow our customer to find great offers in their area provided by our partners.
What we'd like to get from you is a design of several mobile web site pages (screens). For the color choice we were considering unobtrusive combination of white, black and one of the extra colors: purple, green (shades ranging from green apple to mint) or cherry red. Most of the pages will contain images (offers) made by partners with unpredictable color combinations, so our main design should stay minimalist enough to keep customers attention to these images. The pages (screens) are as follows.
1. Welcome screen
- Product logo image
- Short text to thank customers for their choice
- Checkbox with text to accept Terms and Conditions (with link to them)
- Button to continue that is grayed out before the checkbox above is checked
2. List of offers (main screen)
- Header: search bar + 2 icon buttons: location button and menu button
- Info box with a link to profile screen to indicate that authorization is recommended
- Offers: a list of images headed with partner's icon and name aligned left and timer (clock icon + time) aligned right
- Menu: as it's planned, when menu button is pressed, a hover menu from the right is open to display a list of available screens
3. Partner's details and offers
- Header: Partner's name and back button
- Partner's full width logo image
- Short description text of a partner company (up to, say, 500 characters)
- Contact buttons with appropriate icons: "visit their web page" button, call button, location button, like/dislike buttons
- List of their offers as full-width images
- Selected offer should, also, show an "open-down" box with description aligned left and a button to use the offer aligned right
4. Favorites
- Header: Back button, screen name, filter button to open a hover screen to filter by location and other fields
- List of favorite partners with their icon and name aligned left and buttons to "subscribe"/"unsubscribe" (one button) and remove from favorites aligned right
5. Blacklist
- Same as favorites, with just "subscribe"/"unsubscribe" omitted
6. History
- List of taken offers displayed same way as on main screen with actual usage date instead of time remaining
7. Profile
- Header: Back button and screen name
- Rows of inputs for customer to define her age, gender, etc and/or authenticate by Pingwall, Velto, etc.
8. Terms and Conitions
- Text of ToS
9. Language
- List of rows to choose a desired language
As this is our first try of ArtHive platform, please, don't hesitate to ask more questions or correct us on our order. If it feels like there are too many screens requested ahead, please, start with the first few with the intention to complete all of them when we choose you as a winner.
Thank you in advance for your cooperation!

```html
<!DOCTYPE html>
<html lang="en">
<head>
<meta charset="utf-8">
<title>Brivelo – mobile screens</title>
<link href="https://fonts.googleapis.com/css2?family=Poppins:wght@400;500;600;700&family=Varela+Round&display=swap" rel="stylesheet">
<style>
:root{
  --green:#7ed321;
  --green-dark:#3f8a12;
  --purple:#a52bc4;
  --magenta:#c43ad6;
  --canvas:#d3d3d3;
  --band:#ececec;
  --line:#dcdcdc;
  --ink:#222;
  --muted:#777;
  --navy:#2b4a8b;
  --red:#d9232d;
}
*{box-sizing:border-box;margin:0;padding:0}
html,body{width:1200px;height:1110px;overflow:hidden;background:var(--canvas);font-family:"Poppins",sans-serif;color:var(--ink)}
.board{position:relative;width:1200px;height:1110px}
.screen{position:absolute;width:169px;background:#fff;display:flex;flex-direction:column;overflow:hidden}
.bar{height:30px;flex:none;background:var(--green);display:flex;align-items:center;justify-content:space-between;padding:0 8px}
.logo{font-family:"Varela Round",sans-serif;color:#fff;font-size:14px;font-weight:700;letter-spacing:-.2px}
.back{border:1px solid #fff;border-radius:10px;color:#fff;font-size:5.5px;padding:2px 8px;line-height:1}
.user{display:flex;align-items:center;gap:3px;color:#fff;font-size:5px;margin-left:auto;margin-right:5px}
.avatar-dot{width:10px;height:10px;border-radius:50%;background:#8a6a55}
.title-band{height:24px;flex:none;background:var(--band);display:flex;align-items:center;justify-content:space-between;padding:0 10px;font-size:9px;color:#444}
.pill{background:var(--green);color:#fff;font-size:6px;border-radius:8px;padding:3px 13px;line-height:1}
.foot{margin-top:auto;height:26px;flex:none;background:var(--band);display:flex;align-items:center;justify-content:center;font-size:4.6px;color:#666}
.photo{display:block}
.shoes{background:linear-gradient(160deg,#3b3c44 0%,#4a4f5c 40%,#7a5232 60%,#8c8479 100%)}
.dress{background:linear-gradient(180deg,#2b4a86 0%,#5d78a8 40%,#c2281f 65%,#6b1410 100%)}
.group{background:linear-gradient(180deg,#eaeaea 0%,#b9bcc2 50%,#6d7380 80%,#5b4e47 100%)}
.sneaker{background:radial-gradient(circle at 45% 50%,#e0456e 0%,#f06b8a 35%,#fff 70%)}
.office{background:linear-gradient(135deg,#e6e8ec 0%,#cfd4dc 50%,#e9ebee 100%)}
.brand{font-weight:700;font-size:9px;letter-spacing:-.2px;line-height:1}
.brand.sm{font-size:6px;font-weight:600;letter-spacing:.3px}
.sub{font-size:4.5px;color:#555;margin-top:3px;line-height:1.3}
/* welcome */
.locrow{height:22px;flex:none;display:flex;align-items:center;justify-content:flex-end;gap:5px;padding-right:8px}
.locrow .field{width:72px;height:11px;border:1px solid var(--line)}
.hero{position:relative;height:251px;flex:none;text-align:center;padding:26px 14px 0}
.hero .bg{position:absolute;inset:0}
.hero *{position:relative}
.hero h1{font-weight:500;font-size:20px;line-height:1}
.hero h2{font-weight:500;font-size:14px;line-height:1.1}
.hero p{font-size:5.2px;line-height:1.55;color:#555;margin-top:6px}
.check{display:flex;align-items:center;justify-content:center;gap:3px;font-size:4.6px;margin-top:14px;color:#444}
.box{width:7px;height:7px;border:1px solid #888;display:flex;align-items:center;justify-content:center}
.btn{display:inline-block;background:var(--green);color:#fff;border-radius:9px;font-size:7px;padding:4px 15px;margin-top:8px}
/* lists */
.search-band{height:24px;flex:none;background:var(--band);padding:5px}
.search{width:100px;height:14px;background:#fff;border-radius:7px;border:1px solid var(--line);display:flex;align-items:center;justify-content:space-between;padding:0 5px;font-size:4.5px;color:#999}
.info{margin:16px 12px 0;border:1px solid var(--line);height:92px;position:relative;padding:9px 10px;font-size:4.8px;line-height:1.55;text-align:center;color:#555}
.info .btn{position:absolute;left:50%;bottom:-8px;transform:translateX(-50%);font-size:5.5px;padding:4px 11px;margin:0}
.h-list{text-align:center;font-size:10px;font-weight:500;margin:22px 0 8px}
.card{margin:0 10px 19px}
.card .photo{height:77px}
.meta{display:flex;align-items:center;justify-content:space-between;height:22px;border-bottom:1px solid var(--line)}
.meta .left{border-right:1px solid var(--line);padding-right:6px;flex:1}
.timer{display:flex;align-items:center;gap:3px;padding-left:10px}
.num{color:var(--green);font-size:9px;font-weight:500;line-height:1;text-align:center}
.num small{display:block;color:#555;font-size:2.8px;font-weight:500;letter-spacing:.2px}
.colon{color:var(--green);font-size:9px;line-height:1}
/* partner */
.pcard{margin:9px 7px 0;border:1px solid var(--line);height:147px;padding:6px;position:relative}
.pcard .photo{position:absolute;left:6px;top:6px;width:55px;height:40px}
.pcard .txt{margin-left:59px}
.pcard .txt p{font-size:4.2px;line-height:1.55;color:#666;margin-top:4px}
.contacts{position:absolute;left:10px;bottom:8px;display:flex;gap:2px}
.cbtn{height:14px;min-width:14px;background:var(--green);display:flex;align-items:center;justify-content:center;color:#fff;font-size:4.6px;padding:0 3px}
.cbtn.web{padding:0 9px}
.cbtn.p{background:var(--magenta)}
.h-offers{text-align:center;font-size:9px;font-weight:600;margin:14px 0 6px}
.ocard{margin:0 10px 15px}
.ocard .photo{height:77px}
.deal{color:var(--purple);font-size:8px;font-weight:600;line-height:1}
.deal small{display:block;color:var(--green);font-size:5px;font-weight:500}
.expand{margin:-15px 10px 0;height:62px;background:var(--purple);display:flex;align-items:center;gap:8px;padding:0 6px}
.expand p{font-size:4px;line-height:1.5;color:#fff;flex:1}
.expand span{border:1px solid #fff;border-radius:8px;color:#fff;font-size:5px;padding:3px 7px}
.chev{text-align:center;margin-top:8px}
/* favorites / blacklist */
.filters{margin:10px 12px 0;border:1px solid var(--line);padding:8px 8px;display:grid;grid-template-columns:1fr 76px;row-gap:6px;align-items:center;font-size:4.8px;color:#555}
.select{height:12px;border:1px solid var(--line);display:flex;align-items:center;justify-content:space-between;padding:0 5px;font-size:4.5px;color:#666}
.table{margin:16px 12px 0;border:1px solid var(--line)}
.row{display:grid;grid-template-columns:1fr 1fr;height:44px;border-top:1px solid var(--line)}
.row:first-child{border-top:0}
.cell{padding:9px 7px;border-left:1px solid var(--line)}
.cell:first-child{border-left:0}
.icons{display:flex;align-items:center;justify-content:center;gap:5px}
.ic{width:14px;height:14px;border-radius:50%;display:flex;align-items:center;justify-content:center}
.ic.m{background:var(--magenta)}.ic.g{background:var(--green)}.ic.d{background:var(--green-dark)}
/* language */
.choose{color:var(--purple);font-size:5.5px;margin:14px 12px 4px}
.langs{margin:0 10px;border:1px solid var(--line)}
.lang{height:13.6px;border-top:1px solid var(--line);display:flex;align-items:center;gap:4px;padding-left:6px;font-size:4.6px;color:#444}
.lang:first-child{border-top:0}
/* terms */
.terms{margin:12px 12px 0;border:1px solid var(--line);height:294px;padding:10px 10px;font-size:4.3px;line-height:1.85;color:#555}
.terms p+p{margin-top:8px}
/* profile */
.pic{width:58px;height:58px;border-radius:50%;background:#e6e6e6;margin:10px auto 14px;display:flex;align-items:center;justify-content:center}
.input{margin:0 9px 7px;height:16px;border:1px solid var(--line);background:#f9f9f9;display:flex;align-items:center;justify-content:space-between;padding:0 7px;font-size:4.8px;color:#777}
.auth{margin:0 9px 4px;height:17px;display:flex;align-items:center;color:#fff;font-size:5.6px;letter-spacing:.2px}
.auth .sq{width:17px;height:17px;background:rgba(0,0,0,.18);display:flex;align-items:center;justify-content:center}
.auth .sq i{width:5px;height:5px;background:#fff;display:block}
.auth span{flex:1;text-align:center;padding-right:17px}
.auth.pw{background:var(--navy)}.auth.vt{background:var(--red)}
</style>
</head>
<body>
<div class="board">

<!-- Welcome -->
<section class="screen" style="left:85px;top:70px;height:330px">
  <header class="bar"><span class="logo">Brivelo</span>
    <svg width="16" height="10" viewBox="0 0 16 10"><path d="M0 1h16M0 5h16M0 9h16" stroke="#fff" stroke-width="1.5"/></svg></header>
  <div class="locrow">
    <svg width="6" height="8" viewBox="0 0 6 8"><path d="M3 8C1 5 0 4 0 3a3 3 0 016 0c0 1-1 2-3 5z" fill="var(--green)"/></svg>
    <div class="field"></div>
    <svg width="9" height="9" viewBox="0 0 9 9" fill="none" stroke="var(--magenta)"><path d="M4 1h4v7H4M1 4.5h5M4 2.5l2 2-2 2"/></svg>
  </div>
  <div class="hero">
    <div class="bg office" role="img" aria-label="Soft photo of a person working on a laptop"></div>
    <h1>Thank You</h1>
    <h2>for Your choice</h2>
    <p>We are glad you joined us. Discover fresh deals from shops near you every day, save your favourite partners, follow live timers and never miss an offer that fits your style. Set up your profile to get picks made just for you and enjoy smarter shopping.</p>
    <div class="check"><span class="box"><svg width="5" height="5" viewBox="0 0 5 5"><path d="M.5 2.5l1.5 1.5 2.5-3" stroke="#333" fill="none" stroke-width=".8"/></svg></span>Accept Terms and Conditions</div>
    <span class="btn">Submit</span>
  </div>
  <footer class="foot">© 2018 Company Name &nbsp;All right reserved</footer>
</section>

<!-- History -->
<section class="screen" style="left:78px;top:442px;height:522px">
  <header class="bar"><span class="logo">Brivelo</span><span class="back">‹ Back</span></header>
  <div class="title-band">History<span class="pill">Filter</span></div>
  <div class="filters" style="margin-top:12px">
    <span>Filter by Location</span><span class="select">Select Location<span>⌄</span></span>
    <span>Other</span><span class="select"><span></span><span>⌄</span></span>
  </div>
  <div class="h-list" style="margin:10px 0 6px">List of Taken Offers</div>
  <div class="card" style="margin-bottom:40px"><div class="photo shoes" role="img" aria-label="Photo of a man lacing brown leather shoes"></div>
    <div class="meta" style="border:0"><div class="left"><div class="brand sm">FERRO VALE</div><div class="sub">Pellentesque a imperdiet</div></div>
      <div class="timer"><svg width="11" height="11" viewBox="0 0 11 11"><rect x="1" y="2" width="9" height="8" fill="none" stroke="var(--magenta)"/><path d="M1 4h9" stroke="var(--magenta)"/></svg><span class="num">02<small>DATE</small></span><span class="num">05<small>MONTH</small></span><span class="num">18<small>YEAR</small></span></div></div></div>
  <div class="card" style="margin-bottom:40px"><div class="photo dress" role="img" aria-label="Photo of a woman in a flowing red dress by the sea at dusk"></div>
    <div class="meta" style="border:0"><div class="left"><div class="brand sm">LUMARA</div><div class="sub">Aenean facilisis tincidunt</div></div>
      <div class="timer"><svg width="11" height="11" viewBox="0 0 11 11"><rect x="1" y="2" width="9" height="8" fill="none" stroke="var(--magenta)"/><path d="M1 4h9" stroke="var(--magenta)"/></svg><span class="num">02<small>DATE</small></span><span class="num">05<small>MONTH</small></span><span class="num">18<small>YEAR</small></span></div></div></div>
  <div class="card" style="margin-bottom:0"><div class="photo group" role="img" aria-label="Photo of four young people in casual wear against a white brick wall"></div>
    <div class="meta" style="border:0"><div class="left"><div class="brand sm">HALDEN</div><div class="sub">Proin placerat dapibus</div></div>
      <div class="timer"><svg width="11" height="11" viewBox="0 0 11 11"><rect x="1" y="2" width="9" height="8" fill="none" stroke="var(--magenta)"/><path d="M1 4h9" stroke="var(--magenta)"/></svg><span class="num">02<small>DATE</small></span><span class="num">05<small>MONTH</small></span><span class="num">18<small>YEAR</small></span></div></div></div>
  <footer class="foot">© 2018 Company Name &nbsp;All right reserved</footer>
</section>

<!-- Offers list -->
<section class="screen" style="left:298px;top:70px;height:582px">
  <header class="bar"><span class="logo">Brivelo</span><span class="back">‹ Back</span></header>
  <div class="search-band"><div class="search">Search here<svg width="6" height="6" viewBox="0 0 6 6"><circle cx="2.5" cy="2.5" r="2" fill="none" stroke="#777" stroke-width=".7"/><path d="M4 4l1.7 1.7" stroke="#777" stroke-width=".7"/></svg></div></div>
  <div class="info">Sign in to your profile to get offers picked for your area, keep your favourite partners close and see every deal you have taken in one place. Authorization is recommended for the best results.<span class="btn">Go to Profile</span></div>
  <div class="h-list">List of Offers</div>
  <div class="card"><div class="photo shoes" role="img" aria-label="Photo of a man lacing brown leather shoes"></div>
    <div class="meta"><div class="left"><div class="brand sm">FERRO VALE</div><div class="sub">Pellentesque a imperdiet</div></div>
      <div class="timer"><svg width="11" height="11" viewBox="0 0 11 11"><circle cx="5.5" cy="5.5" r="4.5" fill="none" stroke="var(--magenta)" stroke-width="1.3"/><path d="M5.5 3v2.8h2" stroke="var(--magenta)" fill="none"/></svg><span class="num">50<small>HOURS</small></span><span class="colon">:</span><span class="num">08<small>MINS</small></span></div></div></div>
  <div class="card"><div class="photo dress" role="img" aria-label="Photo of a woman in a flowing red dress by the sea at dusk"></div>
    <div class="meta"><div class="left"><div class="brand sm">LUMARA</div><div class="sub">Aenean facilisis tincidunt</div></div>
      <div class="timer"><svg width="11" height="11" viewBox="0 0 11 11"><circle cx="5.5" cy="5.5" r="4.5" fill="none" stroke="var(--magenta)" stroke-width="1.3"/><path d="M5.5 3v2.8h2" stroke="var(--magenta)" fill="none"/></svg><span class="num">24<small>HOURS</small></span><span class="colon">:</span><span class="num">35<small>MINS</small></span></div></div></div>
  <div class="card"><div class="photo group" role="img" aria-label="Photo of four young people in casual wear against a white brick wall"></div>
    <div class="meta"><div class="left"><div class="brand sm">HALDEN</div><div class="sub">Proin placerat dapibus</div></div>
      <div class="timer"><svg width="11" height="11" viewBox="0 0 11 11"><circle cx="5.5" cy="5.5" r="4.5" fill="none" stroke="var(--magenta)" stroke-width="1.3"/><path d="M5.5 3v2.8h2" stroke="var(--magenta)" fill="none"/></svg><span class="num">02<small>HOURS</small></span><span class="colon">:</span><span class="num">37<small>MINS</small></span></div></div></div>
  <footer class="foot">© 2018 Company Name &nbsp;All right reserved</footer>
</section>

<!-- Profile -->
<section class="screen" style="left:300px;top:682px;height:310px">
  <header class="bar"><span class="logo">Brivelo</span><span class="back">‹ Back</span></header>
  <div class="title-band">Profile</div>
  <div class="pic"><svg width="26" height="26" viewBox="0 0 26 26"><circle cx="13" cy="9" r="6" fill="#c9c9c9"/><path d="M2 26c0-7 5-10 11-10s11 3 11 10z" fill="#c9c9c9"/></svg></div>
  <div class="input">Name</div>
  <div class="input">Gender<span>▾</span></div>
  <div class="input">Age<span>▾</span></div>
  <div class="input">Location<span>▾</span></div>
  <div class="auth pw" style="margin-top:14px"><span class="sq"><i></i></span><span>AUTHENTICATE BY PINGWALL</span></div>
  <div class="auth vt"><span class="sq"><i></i></span><span>AUTHENTICATE BY VELTO</span></div>
  <footer class="foot">© 2018 Company Name &nbsp;All right reserved</footer>
</section>

<!-- Partner details -->
<section class="screen" style="left:507px;top:70px;height:694px">
  <header class="bar"><span class="logo">Brivelo</span><span class="user"><span class="avatar-dot"></span>Leo Marsh</span><span class="back">‹ Back</span></header>
  <div class="title-band" style="font-size:8.5px;color:#222">KESTRO</div>
  <div class="pcard">
    <div class="photo sneaker" role="img" aria-label="Product photo of a pink running shoe"></div>
    <div class="txt"><div class="brand">kestro</div>
      <p>Kestro is a wide online store with fashion, home goods and daily needs. Its partner deals bring shoes, bags and sportswear at lower prices, with quick delivery and simple returns for every order placed through the app this season, plus weekly picks for members.</p></div>
    <div class="contacts">
      <span class="cbtn web">Visit their web page</span>
      <span class="cbtn"><svg width="7" height="7" viewBox="0 0 7 7"><path d="M1 .5l1.5 0 .7 1.7-.9.6a4 4 0 002 2l.6-.9 1.6.7v1.4C3 6 1 4 1 .5z" fill="#fff"/></svg></span>
      <span class="cbtn"><svg width="5" height="7" viewBox="0 0 6 8"><path d="M3 8C1 5 0 4 0 3a3 3 0 016 0c0 1-1 2-3 5z" fill="#fff"/></svg></span>
      <span class="cbtn p"><svg width="7" height="7" viewBox="0 0 7 7"><path d="M.5 3h1.5v3.5H.5zM2.5 3l1.5-2.5c.6 0 .8.4.7 1L4.5 2.5H6.3c.4 0 .6.3.5.7L6.2 6c-.1.3-.3.5-.6.5H2.5z" fill="none" stroke="#fff" stroke-width=".6"/></svg></span>
      <span class="cbtn p"><svg width="7" height="7" viewBox="0 0 7 7" style="transform:scaleY(-1)"><path d="M.5 3h1.5v3.5H.5zM2.5 3l1.5-2.5c.6 0 .8.4.7 1L4.5 2.5H6.3c.4 0 .6.3.5.7L6.2 6c-.1.3-.3.5-.6.5H2.5z" fill="none" stroke="#fff" stroke-width=".6"/></svg></span>
    </div>
  </div>
  <div class="h-offers">OFFERS</div>
  <div class="ocard"><div class="photo shoes" role="img" aria-label="Photo of a man lacing brown leather shoes"></div>
    <div class="meta" style="height:30px;border:0"><div class="left" style="padding-left:10px"><div class="brand">kestro</div><div class="sub">Kestro</div></div><div style="padding-left:26px;flex:1"><div class="deal"><small>GET NOW</small>25 % OFF</div></div></div></div>
  <div class="ocard"><div class="photo dress" role="img" aria-label="Photo of a woman in a flowing red dress by the sea at dusk"></div>
    <div class="meta" style="height:30px;border:0"><div class="left" style="padding-left:10px"><div class="brand">kestro</div><div class="sub">Kestro</div></div><div style="padding-left:26px;flex:1"><div class="deal"><small>GET NOW</small>25 % OFF</div></div></div></div>
  <div class="ocard"><div class="photo group" role="img" aria-label="Photo of four young people in casual wear against a white brick wall"></div>
    <div class="meta" style="height:30px;border:0"><div class="left" style="padding-left:10px"><div class="brand">kestro</div><div class="sub">Kestro</div></div><div style="padding-left:22px;flex:1"><div class="deal"><small>GET NOW</small>30 % OFF</div></div></div>
    <svg width="10" height="5" viewBox="0 0 10 5" style="display:block;margin:-1px 0 0 88px"><path d="M0 5L5 0l5 5z" fill="var(--purple)"/></svg></div>
  <div class="expand"><p>Take this deal in store or online before the timer runs out. Show the code at checkout and the discount is added to your order automatically, no extra steps.</p><span>Click here</span></div>
  <div class="chev"><svg width="12" height="7" viewBox="0 0 12 7"><path d="M1 1l5 5 5-5" fill="none" stroke="#777" stroke-width="1.2"/></svg></div>
  <footer class="foot">© 2018 Company Name &nbsp;All right reserved</footer>
</section>

<!-- Favorites -->
<section class="screen" style="left:714px;top:70px;height:406px">
  <header class="bar"><span class="logo">Brivelo</span><span class="back">‹ Back</span></header>
  <div class="title-band">Favorites<span class="pill">Filter</span></div>
  <div class="filters"><span>Filter by Products</span><span class="select">Product<span>⌄</span></span><span>Filter by Offers</span><span class="select">Offers<span>⌄</span></span></div>
  <div class="table">
    <div class="row"><div class="cell"><div class="brand">kestro</div><div class="sub">Aenean facilisis tincidunt</div></div><div class="cell icons"><span class="ic m"></span><span class="ic g"></span><span class="ic d"><svg width="7" height="6" viewBox="0 0 7 6"><path d="M3.5 5.5L.8 2.8a1.4 1.4 0 012.7-2 1.4 1.4 0 012.7 2z" fill="none" stroke="#fff" stroke-width=".7"/></svg></span></div></div>
    <div class="row"><div class="cell"><div class="brand sm" style="font-size:8px">LUMARA</div><div class="sub">Aenean facilisis tincidunt</div></div><div class="cell icons"><span class="ic m"></span><span class="ic g"></span><span class="ic d"><svg width="7" height="6" viewBox="0 0 7 6"><path d="M3.5 5.5L.8 2.8a1.4 1.4 0 012.7-2 1.4 1.4 0 012.7 2z" fill="none" stroke="#fff" stroke-width=".7"/></svg></span></div></div>
    <div class="row"><div class="cell"><div class="brand" style="font-size:8px;color:#2a62b5">Brandell</div><div class="sub">Aenean facilisis tincidunt</div></div><div class="cell icons"><span class="ic m"></span><span class="ic g"></span><span class="ic d"><svg width="7" height="6" viewBox="0 0 7 6"><path d="M3.5 5.5L.8 2.8a1.4 1.4 0 012.7-2 1.4 1.4 0 012.7 2z" fill="none" stroke="#fff" stroke-width=".7"/></svg></span></div></div>
    <div class="row"><div class="cell"><div class="brand sm" style="font-size:5px">HALDEN</div><div class="sub">Aenean facilisis tincidunt</div></div><div class="cell icons"><span class="ic m"></span><span class="ic g"></span><span class="ic d"><svg width="7" height="6" viewBox="0 0 7 6"><path d="M3.5 5.5L.8 2.8a1.4 1.4 0 012.7-2 1.4 1.4 0 012.7 2z" fill="none" stroke="#fff" stroke-width=".7"/></svg></span></div></div>
    <div class="row"><div class="cell"><div class="brand sm" style="font-size:5px">FERRO VALE</div><div class="sub">Curabitur vel mi sit amet magna malesuada ult</div></div><div class="cell icons"><span class="ic m"></span><span class="ic g"></span><span class="ic d"><svg width="7" height="6" viewBox="0 0 7 6"><path d="M3.5 5.5L.8 2.8a1.4 1.4 0 012.7-2 1.4 1.4 0 012.7 2z" fill="none" stroke="#fff" stroke-width=".7"/></svg></span></div></div>
  </div>
  <footer class="foot">© 2018 Company Name &nbsp;All right reserved</footer>
</section>

<!-- Blacklist -->
<section class="screen" style="left:911px;top:70px;height:408px">
  <header class="bar"><span class="logo">Brivelo</span><span class="back">‹ Back</span></header>
  <div class="title-band">Blacklist<span class="pill">Filter</span></div>
  <div class="filters"><span>Filter by Products</span><span class="select">Product<span>⌄</span></span><span>Filter by Offers</span><span class="select">Offers<span>⌄</span></span></div>
  <div class="table">
    <div class="row"><div class="cell"><div class="brand">kestro</div><div class="sub">Aenean facilisis tincidunt</div></div><div class="cell"><div class="brand sm" style="color:#e07b1a">NESTWELL</div><div class="sub">Aenean facilisis tincidunt</div></div></div>
    <div class="row"><div class="cell"><div class="brand sm" style="font-size:8px">LUMARA</div><div class="sub">Aenean facilisis tincidunt</div></div><div class="cell"><div class="brand">corvo</div><div class="sub">Aenean facilisis tincidunt</div></div></div>
    <div class="row"><div class="cell"><div class="brand" style="font-size:8px;color:#2a62b5">Brandell</div><div class="sub">Aenean facilisis tincidunt</div></div><div class="cell"><div class="brand" style="font-weight:400;color:#b08a55">tilvo</div><div class="sub">Aenean facilisis tincidunt</div></div></div>
    <div class="row"><div class="cell"><div class="brand sm" style="font-size:5px">HALDEN</div><div class="sub">Aenean facilisis tincidunt</div></div><div class="cell"><div class="brand" style="font-weight:500">Ornat</div><div class="sub">Aenean facilisis tincidunt</div></div></div>
    <div class="row"><div class="cell"><div class="brand sm" style="font-size:5px">FERRO VALE</div><div class="sub">Curabitur vel mi sit amet magna malesuada ult</div></div><div class="cell"><div class="brand sm">pinecrest</div><div class="sub">Curabitur vel mi sit amet magna malesuada ult</div></div></div>
  </div>
  <footer class="foot">© 2018 Company Name &nbsp;All right reserved</footer>
</section>

<!-- Language -->
<section class="screen" style="left:716px;top:507px;height:301px">
  <header class="bar"><span class="logo">Brivelo</span><span class="back">‹ Back</span></header>
  <div class="title-band">Language</div>
  <div class="choose">Choose a Language</div>
  <div class="langs">
    <div class="lang">›&nbsp;Spanish</div><div class="lang">›&nbsp;English</div><div class="lang">›&nbsp;Hindi</div><div class="lang">›&nbsp;Italian</div><div class="lang">›&nbsp;Swedish</div><div class="lang">›&nbsp;Russian</div><div class="lang">›&nbsp;German</div><div class="lang">›&nbsp;Chinese</div><div class="lang">›&nbsp;Arabic</div><div class="lang">›&nbsp;Japanese</div><div class="lang">›&nbsp;Italy</div><div class="lang">›&nbsp;Dutch</div><div class="lang">›&nbsp;French</div>
  </div>
  <footer class="foot">© 2018 Company Name &nbsp;All right reserved</footer>
</section>

<!-- Terms -->
<section class="screen" style="left:914px;top:510px;height:407px">
  <header class="bar"><span class="logo">Brivelo</span><span class="back">‹ Back</span></header>
  <div class="title-band">Terms and Conditions</div>
  <div class="terms">
    <p>By using this service you agree to these terms. Offers are supplied by partner stores and may change or end at any time without notice.</p>
    <p>Each deal is valid only until its timer runs out. Discounts apply once per customer unless the partner states otherwise. We are not the seller of any goods shown in the app and do not handle payments or returns.</p>
    <p>Your profile data such as age, gender and location is used only to pick offers for you. You may edit or remove it at any time from the profile screen. Sign in through a linked account shares your name and email with us. We never sell personal data to third parties. Partners receive only anonymous usage counts for their own offers. You are responsible for keeping your account safe and for any use made under it. We may suspend accounts that misuse codes or break local laws. These terms may be updated, and continued use of the app means you accept the new version.</p>
  </div>
  <footer class="foot">© 2018 Company Name &nbsp;All right reserved</footer>
</section>

</div>
</body>
</html>
```